Cover für ein Taschenbuch zum Thema Ruhestand gesucht!
Zielgruppe
Unsere Zielgruppe sind Senioren, bzw. Menschen im Alter 50+. Es handelt sich bei dem Buch um einen Ratgeber zum Thema 'Ruhestand'. Allerdings wird das Buch ebenso von einer jüngeren Zielgruppe gekauft, da der Ratgeber auch gerne an Eltern oder Großeltern verschenkt wird.
Aufgabenstellung
siehe Dateiupload
Format: 5,25' x 8'

```html
<!DOCTYPE html>
<html lang="de">
<head>
<meta charset="utf-8">
<title>IHR Ruhestand – Buchcover</title>
<link href="https://fonts.googleapis.com/css2?family=Tinos:wght@400;700&family=Nunito:wght@500&family=Asap:wght@400&display=swap" rel="stylesheet">
<style>
  :root {
    --sky-top: #e4e8ec;
    --sky-low: #b9c6d2;
    --sea-far: #6f93b3;
    --sea-mid: #3f72a0;
    --sea-near: #3a6690;
    --rock: #7d7a74;
    --grass: #5a7a3a;
    --ink: #111111;
    --accent-blue: #3f77ad;
    --circle-blue: rgba(86, 124, 156, 0.92);
    --circle-pale: #e2eccc;
    --author: #f1f1ee;
  }
  * { margin: 0; padding: 0; box-sizing: border-box; }
  html, body { width: 788px; height: 1200px; overflow: hidden; background: #ffffff; }
  .cover {
    position: relative;
    width: 788px;
    height: 1200px;
    overflow: hidden;
  }
  .cover-photo {
    position: absolute;
    inset: 0;
    background:
      linear-gradient(to bottom,
        var(--sky-top) 0%,
        var(--sky-low) 22%,
        var(--sea-far) 27%,
        var(--sea-mid) 45%,
        var(--sea-near) 78%,
        var(--rock) 84%,
        #8f8a80 94%,
        var(--grass) 98%);
  }
  .title {
    position: absolute;
    top: 52px;
    left: 0;
    width: 788px;
    text-align: center;
    font-family: "Tinos", "Times New Roman", serif;
    font-weight: 700;
    font-size: 82px;
    line-height: 1;
    color: var(--ink);
    z-index: 2;
  }
  .subtitle {
    position: absolute;
    top: 162px;
    left: 0;
    width: 788px;
    text-align: center;
    font-family: "Nunito", Arial, sans-serif;
    font-weight: 500;
    font-size: 33px;
    color: var(--accent-blue);
    z-index: 2;
  }
  .dot {
    position: absolute;
    border-radius: 50%;
    z-index: 1;
  }
  .dot-top { left: 538px; top: -4px; width: 250px; height: 250px; background: var(--circle-pale); }
  .dot-small { left: 2px; top: 890px; width: 126px; height: 126px; background: var(--circle-pale); }
  .blurb {
    position: absolute;
    left: 48px;
    top: 542px;
    width: 396px;
    height: 396px;
    border-radius: 50%;
    background: var(--circle-blue);
    display: flex;
    align-items: center;
    justify-content: center;
    text-align: center;
    font-family: "Asap", Arial, sans-serif;
    font-size: 34px;
    line-height: 1.22;
    color: #ffffff;
    z-index: 1;
  }
  .author {
    position: absolute;
    top: 1098px;
    left: 0;
    width: 788px;
    text-align: center;
    font-family: "Tinos", "Times New Roman", serif;
    font-size: 48px;
    letter-spacing: 0.55em;
    padding-left: 0.55em;
    color: var(--author);
    z-index: 2;
  }
</style>
</head>
<body>
  <main class="cover">
    <div class="cover-photo" role="img" aria-label="Foto: älterer Mann mit Hut und kariertem Hemd steht am Seeufer auf Felsen und blickt auf das blaue Wasser, in der Ferne ein Segelboot"></div>
    <span class="dot dot-top"></span>
    <span class="dot dot-small"></span>
    <h1 class="title">IHR Ruhestand</h1>
    <p class="subtitle">Das Beste kommt immer zum Schluss!</p>
    <p class="blurb">Die<br>besten Strate-<br>gien und Tipps,<br>mit denen Sie Ihre<br>Rentenzeit in vollen<br>Zügen genießen<br>können</p>
    <p class="author">Bernhard Keller</p>
  </main>
</body>
</html>
```